Local fast-growing company in the service sector

We are looking for a modern business card design, which should also appear on our letterheads

Target Market(s)

Private and industrial sectors

Contact Information for Business Card

Vorname Name
Kellberger Str. 18
74321 Bietigheim
Tel.: 07146-839214-0
Name@agentur-kvtl.de

Colors
9d9d9d
919191
aaaaaa

Requirements
Must have
• The logo (file) in silver

```html
<!DOCTYPE html>
<html lang="de">
<head>
<meta charset="utf-8">
<title>KVTL Visitenkarte</title>
<link rel="stylesheet" href="https://fonts.googleapis.com/css2?family=Lato:wght@300;400;700&display=swap">
<style>
  :root {
    --page-bg: #e9e9e9;
    --card-light: #ffffff;
    --card-mid: #f0f0f0;
    --card-edge: #e2e2e2;
    --silver: #aaaaaa;
    --silver-mid: #9d9d9d;
    --band: #7f7f83;
    --band-line: #919191;
    --text-grey: #8a8a8a;
    --text-light: #ffffff;
  }
  * { margin: 0; padding: 0; box-sizing: border-box; }
  html, body {
    width: 1200px; height: 780px; overflow: hidden;
    background: var(--page-bg);
    font-family: "Lato", sans-serif;
  }
  .canvas {
    width: 1200px; height: 780px;
    display: flex; align-items: center; justify-content: center;
  }
  .card {
    position: relative;
    width: 940px; height: 608px;
    background: linear-gradient(160deg, var(--card-light) 0%, var(--card-mid) 55%, var(--card-edge) 100%);
    box-shadow: 0 10px 30px rgba(0,0,0,0.12);
    overflow: hidden;
  }
  .brand {
    position: absolute; left: 300px; top: 70px;
    display: flex; flex-direction: column;
  }
  .brand-row { display: flex; align-items: center; gap: 26px; }
  .brand-dot {
    width: 92px; height: 92px; border-radius: 50%;
    background: linear-gradient(145deg, #d6d6d6, var(--silver));
  }
  .brand-name {
    font-weight: 700; font-size: 128px; line-height: 1;
    letter-spacing: 4px; color: var(--silver);
  }
  .brand-web {
    margin-left: 118px; margin-top: 4px;
    font-weight: 300; font-size: 44px; letter-spacing: 3px;
    color: var(--silver);
  }
  .name-band {
    position: absolute; left: 0; right: 0; top: 322px; height: 64px;
    background: var(--band);
    border-bottom: 12px solid var(--card-light);
    box-shadow: 0 12px 0 0 var(--band-line);
  }
  .person-name {
    position: absolute; left: 300px; top: 13px;
    font-weight: 400; font-size: 38px; letter-spacing: 1px;
    color: var(--text-light); text-transform: uppercase; line-height: 1;
  }
  .contact {
    position: absolute; left: 300px; top: 428px;
    list-style: none; color: var(--text-grey);
    font-weight: 300; font-size: 28px; line-height: 38px;
  }
  .contact li { display: flex; align-items: center; gap: 10px; }
  .contact .icon { width: 26px; height: 26px; flex: none; }
</style>
</head>
<body>
<main class="canvas">
  <section class="card">
    <div class="brand">
      <div class="brand-row">
        <span class="brand-dot"></span>
        <span class="brand-name">KVTL</span>
      </div>
      <span class="brand-web">agentur-kvtl.de</span>
    </div>

    <div class="name-band">
      <span class="person-name">Lena Hartmann</span>
    </div>

    <ul class="contact">
      <li>Kellberger Str. 18</li>
      <li>74321 Bietigheim</li>
      <li>
        <svg class="icon" viewBox="0 0 26 26" aria-hidden="true">
          <circle cx="13" cy="13" r="12" fill="var(--text-grey)"/>
          <path d="M8 9.5c0-1 1-1.8 2-1.5l1 2.2-1.2 1.2a8 8 0 0 0 4 4l1.2-1.2 2.2 1c.3 1-.5 2-1.5 2A8 8 0 0 1 8 9.5z" fill="#fff"/>
        </svg>
        07146-839214-0
      </li>
      <li>
        <svg class="icon" viewBox="0 0 26 26" aria-hidden="true">
          <circle cx="13" cy="13" r="12" fill="var(--text-grey)"/>
          <rect x="7" y="9" width="12" height="8.5" fill="#fff"/>
          <path d="M7 9l6 5 6-5" fill="none" stroke="var(--text-grey)" stroke-width="1.2"/>
        </svg>
        Name@agentur-kvtl.de
      </li>
    </ul>
  </section>
</main>
</body>
</html>
```